business card deign

Logo needs the following on it.
1. attached logo
2. Tagline - "If it chills a drink or livens the night...we handle it!"
3. Name- Dalton Pikes, Founder and CPO
4. Address - 412 E. Carver Avenue, Ste 2207, Tampa, FL. 33917
5. Phone - 555.318.4726

```html
<!DOCTYPE html>
<html lang="en">
<head>
<meta charset="utf-8">
<title>Talvory Business Card</title>
<link href="https://fonts.googleapis.com/css2?family=Montserrat:wght@400;500;600;700&display=swap" rel="stylesheet">
<style>
  :root {
    --backdrop: #e9e8ea;
    --card-light: #ffffff;
    --card-dark: #1f1f1f;
    --ink: #111111;
    --ink-soft: #1c1c1c;
    --brand-dark: #0c0c0c;
    --tagline: #d6d6d6;
  }
  * { margin: 0; padding: 0; box-sizing: border-box; }
  html, body {
    width: 1200px;
    height: 1108px;
    overflow: hidden;
    background: var(--backdrop);
    font-family: "Montserrat", sans-serif;
  }
  .card {
    position: absolute;
    width: 740px;
    height: 443px;
  }
  .card--front { left: 241px; top: 68px; background: var(--card-light); color: var(--ink); }
  .card--back { left: 248px; top: 589px; background: var(--card-dark); }

  .brand-name {
    position: absolute;
    left: 35px;
    top: 67px;
    font-family: "Montserrat", sans-serif;
    font-weight: 700;
    font-size: 42px;
    letter-spacing: 20px;
    line-height: 1;
    color: var(--ink);
    white-space: nowrap;
  }
  .person { position: absolute; left: 35px; top: 218px; }
  .person__name { font-weight: 700; font-size: 26px; line-height: 1.2; }
  .person__role { font-weight: 400; font-size: 16px; margin-top: 0; color: var(--ink-soft); }

  .divider {
    position: absolute;
    left: 35px;
    top: 288px;
    width: 663px;
    height: 2px;
    background: var(--ink);
  }
  .contacts {
    position: absolute;
    left: 37px;
    top: 311px;
    list-style: none;
  }
  .contacts__item {
    display: flex;
    align-items: center;
    gap: 10px;
    font-size: 15.5px;
    height: 32px;
    color: var(--ink-soft);
  }
  .contacts__icon { width: 16px; height: 16px; fill: var(--ink); flex: none; }
  .address {
    position: absolute;
    left: 469px;
    top: 358px;
    font-size: 15.5px;
    line-height: 1.35;
    color: var(--ink-soft);
  }

  .brand-name--back {
    left: 0;
    right: 0;
    top: 276px;
    text-align: center;
    padding-left: 22px;
    font-size: 46px;
    letter-spacing: 22px;
    color: var(--brand-dark);
  }
  .tagline {
    position: absolute;
    left: 0;
    right: 0;
    top: 387px;
    text-align: center;
    font-size: 16.5px;
    color: var(--tagline);
  }
</style>
</head>
<body>
  <section class="card card--front">
    <div class="brand-name">TALVORY</div>
    <div class="person">
      <div class="person__name">Dalton Pikes</div>
      <div class="person__role">Founder and CPO</div>
    </div>
    <div class="divider"></div>
    <ul class="contacts">
      <li class="contacts__item">
        <svg class="contacts__icon" viewBox="0 0 24 24" aria-hidden="true"><path d="M6.6 10.8a15.2 15.2 0 0 0 6.6 6.6l2.2-2.2a1 1 0 0 1 1-.25 11.4 11.4 0 0 0 3.6.57 1 1 0 0 1 1 1V20a1 1 0 0 1-1 1A17 17 0 0 1 3 4a1 1 0 0 1 1-1h3.5a1 1 0 0 1 1 1c0 1.25.2 2.45.57 3.6a1 1 0 0 1-.25 1z"/></svg>
        <span>555.318.4726</span>
      </li>
      <li class="contacts__item">
        <svg class="contacts__icon" viewBox="0 0 24 24" aria-hidden="true"><path d="M3 6.5V19h18V6.5l-9 6z M3.5 5h17L12 10.7z"/></svg>
        <span>info@talvory.com</span>
      </li>
      <li class="contacts__item">
        <svg class="contacts__icon" viewBox="0 0 24 24" aria-hidden="true"><circle cx="12" cy="12" r="9" fill="none" stroke="#111" stroke-width="2"/><path d="M3 12h18M12 3c3 3.2 3 14.8 0 18M12 3c-3 3.2-3 14.8 0 18" fill="none" stroke="#111" stroke-width="1.6"/></svg>
        <span>www.talvory.com</span>
      </li>
    </ul>
    <div class="address">412 E. Carver Avenue, Ste 2207,<br>Tampa, FL. 33917</div>
  </section>

  <section class="card card--back">
    <div class="brand-name brand-name--back">TALVORY</div>
    <p class="tagline">If it chills a drink or livens the night...we handle it</p>
  </section>
</body>
</html>
```